Mosquito Coastal & Garden Pest Control

The uploaded logo must be integrated as the main theme of the card. I would like it to be modern and eye catching. Maybe some backround images or light silver metallic background.
Space enough at the base for contact info to be put in- phone numbers,emails,names,website.
Space on the back for short blog and lines for hand writing..calling card.
Commercial- golf courses, schools, outdoor function properties, pre event treatments.
Residential- retirement villages, townhome complexes and general houses
Management

```html
<!DOCTYPE html>
<html lang="en">
<head>
<meta charset="utf-8">
<title>Eastbay Pest Co. – Business Card</title>
<link href="https://fonts.googleapis.com/css2?family=Cinzel:wght@400;500&display=swap" rel="stylesheet">
<style>
  :root {
    --backdrop: #3b3b3d;
    --silver-light: #fbfbfb;
    --silver-mid: #dcdcdc;
    --silver-dark: #bdbdbd;
    --ink: #1f1f22;
    --band: #1e1f23;
    --accent: #e8202e;
    --contact-text: #f2f2f2;
    --rule: #6a6a6a;
  }
  * { box-sizing: border-box; margin: 0; padding: 0; }
  html, body {
    width: 1105px; height: 1200px; overflow: hidden;
    background: var(--backdrop);
  }
  .card {
    position: absolute;
    left: 196px;
    width: 720px;
    height: 412px;
    overflow: hidden;
    background: radial-gradient(ellipse at 52% 45%, var(--silver-light) 0%, var(--silver-mid) 55%, var(--silver-dark) 100%);
    box-shadow: 0 6px 14px rgba(0,0,0,0.45);
    font-family: "Cinzel", "Times New Roman", serif;
  }
  .card--front { top: 146px; }
  .card--back { top: 602px; }

  .brand { position: absolute; left: 25px; top: 42px; }
  .brand__name {
    font-size: 32px; font-weight: 500; color: var(--ink);
    letter-spacing: 0.5px; line-height: 1;
  }
  .brand__tagline {
    margin-top: 6px; font-size: 12.5px; color: var(--ink);
    letter-spacing: 0.4px;
  }

  .person { position: absolute; left: 25px; top: 164px; }
  .person__name { font-size: 28px; font-weight: 500; color: var(--accent); line-height: 1; }
  .person__role { margin-top: 12px; font-size: 19px; color: var(--ink); }

  .accent-stripe {
    position: absolute; left: 200px; right: 0; top: 266px; height: 8px;
    background: var(--accent);
  }
  .contact-band {
    position: absolute; left: 0; right: 0; top: 278px; bottom: 0;
    background: var(--band);
  }
  .contacts { position: absolute; left: 30px; top: 30px; list-style: none; }
  .contacts__item {
    display: flex; align-items: center; gap: 12px;
    height: 30.5px; font-size: 17px; color: var(--contact-text);
    letter-spacing: 0.3px;
  }
  .contacts__icon { width: 16px; height: 16px; fill: var(--accent); flex: none; }

  .brand-dot {
    position: absolute; border-radius: 50%; background: var(--accent);
  }
  .card--front .brand-dot { width: 84px; height: 84px; right: 46px; top: 24px; }
  .card--back .brand-dot { width: 84px; height: 84px; left: 549px; top: 288px; }

  .note-line {
    position: absolute; left: 25px; width: 663px; height: 0;
    border-top: 1.5px dotted var(--rule);
  }
  .note-line--short { width: 453px; }
  .note-line--mid { width: 497px; }
</style>
</head>
<body>
  <section class="card card--front" aria-label="Business card front">
    <div class="brand">
      <div class="brand__name">Eastbay Pest Co.</div>
      <div class="brand__tagline">COASTAL &amp; GARDEN PEST CONTROL</div>
    </div>

    <div class="person">
      <div class="person__name">Daniel Hart</div>
      <div class="person__role">CEO/Founder</div>
    </div>

    <div class="accent-stripe"></div>
    <div class="contact-band">
      <ul class="contacts">
        <li class="contacts__item">
          <svg class="contacts__icon" viewBox="0 0 16 16" aria-hidden="true"><path d="M3.6 1.2l2.3 2.4-1.3 2a8.6 8.6 0 0 0 5.8 5.8l2-1.3 2.4 2.3-1.4 2.2C7.2 15 1 8.8 1.4 2.6z"/></svg>
          555 210 4817
        </li>
        <li class="contacts__item">
          <svg class="contacts__icon" viewBox="0 0 16 16" aria-hidden="true"><path d="M1 3.5h14v1L8 9 1 4.5z M1 6l7 4.5L15 6v7H1z"/></svg>
          HELLO@EASTBAYPEST.COM
        </li>
        <li class="contacts__item">
          <svg class="contacts__icon" viewBox="0 0 16 16" aria-hidden="true"><circle cx="8" cy="8" r="7"/><path d="M8 1v14M1 8h14M3 4h10M3 12h10" stroke="#1e1f23" stroke-width="1" fill="none"/></svg>
          WWW.EASTBAYPEST.COM
        </li>
      </ul>
      <div class="brand-dot" aria-hidden="true"></div>
    </div>
  </section>

  <section class="card card--back" aria-label="Business card back with note lines">
    <div class="note-line" style="top:54px"></div>
    <div class="note-line" style="top:98px"></div>
    <div class="note-line" style="top:141px"></div>
    <div class="note-line" style="top:184px"></div>
    <div class="note-line" style="top:232px"></div>
    <div class="note-line note-line--short" style="top:278px"></div>
    <div class="note-line note-line--mid" style="top:332px"></div>
    <div class="note-line note-line--mid" style="top:375px"></div>
    <div class="brand-dot" aria-hidden="true"></div>
  </section>
</body>
</html>
```